Business card - Harbor Crest Builders

Design a business card utilizing the given logo.
colors we like: Black, greys, Teal, blues.
Tri color card, horizontal orientation likely
Logo and name likely best on top.
Info on card:

Dennis Farrow
#8 - 4815 Alder Ridge Blvd.
Surrey, B.C. V3K 2R9

778.555.0193
dennisfarrow@tellmail.ca

Slogan: "Building Dreams"

We are a construction company that specializes in new home construction on the West coast of BC Canada. Open Concepts designs of high end homes.

```html
<!DOCTYPE html>
<html lang="en">
<head>
<meta charset="utf-8">
<title>Harbor Crest Builders – Business Card</title>
<link rel="stylesheet" href="https://fonts.googleapis.com/css2?family=Exo+2:wght@600;700&family=Roboto+Condensed:wght@400&display=swap">
<style>
  :root {
    --stage: #8a8a8a;
    --card-black: #000000;
    --card-grey: #9a9a9a;
    --card-white: #ffffff;
    --ink: #111111;
    --ink-soft: #2a2a2a;
  }
  * { box-sizing: border-box; margin: 0; padding: 0; }
  html, body {
    width: 1200px; height: 1000px; overflow: hidden;
    background: var(--stage);
  }
  .card {
    position: absolute;
    left: 120px; top: 220px;
    width: 960px; height: 560px;
    background: var(--card-black);
    overflow: hidden;
    box-shadow: 0 6px 18px rgba(0,0,0,.35);
  }
  .card-bands { position: absolute; inset: 0; }
  .brand {
    position: absolute;
    left: 156px; top: 60px;
    display: flex; align-items: center;
  }
  .brand-dot {
    width: 118px; height: 118px; border-radius: 50%;
    background: var(--ink);
  }
  .brand-divider {
    width: 3px; height: 128px;
    background: var(--ink);
    margin: 0 42px 0 52px;
  }
  .brand-name {
    display: flex; flex-direction: column; align-items: flex-end;
    font-family: "Exo 2", sans-serif; font-weight: 700;
    color: var(--ink); text-transform: uppercase; line-height: 1;
  }
  .brand-name .line-main { font-size: 56px; letter-spacing: 1px; }
  .brand-name .line-sub { font-size: 30px; letter-spacing: 3px; margin-top: 4px; }
  .person {
    position: absolute;
    right: 124px; top: 250px;
    text-align: right;
  }
  .person-name {
    font-family: "Exo 2", sans-serif; font-weight: 700;
    font-size: 38px; letter-spacing: 1.5px; color: var(--ink);
  }
  .person-title {
    font-family: "Roboto Condensed", sans-serif;
    font-size: 20px; color: var(--ink-soft); margin-top: 2px;
  }
  .contact {
    position: absolute;
    left: 318px; top: 432px;
    list-style: none;
    font-family: "Roboto Condensed", sans-serif;
    font-size: 22px; color: var(--ink-soft);
  }
  .contact li { display: flex; align-items: center; height: 30px; }
  .contact svg { width: 20px; height: 20px; margin-right: 14px; flex: none; }
</style>
</head>
<body>
  <main class="card">
    <svg class="card-bands" viewBox="0 0 960 560" width="960" height="560" aria-hidden="true">
      <path d="M26 0 H960 V560 H317 C130 520 20 300 26 0 Z" fill="var(--card-grey)"/>
      <path d="M66 0 H960 V560 H420 C200 500 60 330 66 0 Z" fill="var(--card-white)"/>
    </svg>

    <header class="brand">
      <span class="brand-dot"></span>
      <span class="brand-divider"></span>
      <h1 class="brand-name">
        <span class="line-main">Harbor Crest</span>
        <span class="line-sub">Builders</span>
      </h1>
    </header>

    <section class="person">
      <h2 class="person-name">Dennis Farrow</h2>
      <p class="person-title">Managing Director</p>
    </section>

    <ul class="contact">
      <li>
        <svg viewBox="0 0 20 20" aria-hidden="true"><rect width="20" height="20" rx="4" fill="var(--ink)"/><path d="M7 4 l2 3 -1.5 1.5 c1 2 2 3 4 4 L13 11 l3 2 -1.5 2.5 C9 15 5 11 4.5 5.5 Z" fill="#fff"/></svg>
        778.555.0193
      </li>
      <li>
        <svg viewBox="0 0 20 20" aria-hidden="true"><rect width="20" height="20" rx="4" fill="var(--ink)"/><rect x="4" y="6" width="12" height="8" fill="#fff"/><path d="M4 6 L10 11 L16 6" fill="none" stroke="var(--ink)" stroke-width="1.4"/></svg>
        dennisfarrow@tellmail.ca
      </li>
      <li>
        <svg viewBox="0 0 20 20" aria-hidden="true"><rect width="20" height="20" rx="4" fill="var(--ink)"/><path d="M10 3.5 a4.5 4.5 0 0 1 4.5 4.5 c0 3.5 -4.5 8.5 -4.5 8.5 s-4.5 -5 -4.5 -8.5 A4.5 4.5 0 0 1 10 3.5 Z" fill="#fff"/><circle cx="10" cy="8" r="1.8" fill="var(--ink)"/></svg>
        #8 - 4815 Alder Ridge Blvd. Surrey, B.C. V3K 2R9
      </li>
    </ul>
  </main>
</body>
</html>
```